Animal Horse & Bedding Company Needs a Website Coded & Designed

We need a website for a new animal bedding and feed company that is visually grabbing and vibrant. We would like to see a website that displays trust, quality and confidence. Needs to be responsive and mobile friendly for all browsers and coded for both Android & IOS. SEO is also important.

Joomla or Wordpress – must be both desktop and mobile friendly with fast page load speed. Need the ability to edit ourselves in Wordpress or Joomla.

Full details attached below with some layout and content ideas.

Coding

Coded - Design and coding required

Number of Pages Required

5+ page

Font styles to use
Sans Serif

Requirements
Must have
• Needs to be responsive and mobile friendly for all browsers and coded for both Android & IOS. SEO is also important.

Wordpress – must be both desktop and mobile friendly with fast page load speed. Need the ability to edit ourselves in Wordpress.

Logo Colours:
Dark Brown
CMYK: 50 / 70 / 80 / 70
Pantone: 4625C

Orange
CMYK: 0 / 50 / 100 / 0
Pantone: 144C
Nice to have
• Use picture of building attached and super impose logo on building.

```html
<!DOCTYPE html>
<html lang="en">
<head>
<meta charset="utf-8">
<title>Harvest Hollow – Bedding &amp; Feed</title>
<link href="https://fonts.googleapis.com/css2?family=Oswald:wght@500&family=Source+Sans+3:wght@400;600;700&display=swap" rel="stylesheet">
<style>
:root{
  --brown:#3c2415;
  --brown-mid:#4a2c18;
  --orange:#f7a11a;
  --orange-deep:#f39200;
  --text:#555;
  --white:#fff;
}
*{box-sizing:border-box;margin:0;padding:0}
html,body{width:1200px;height:2808px;overflow:hidden}
body{position:relative;font-family:"Source Sans 3",sans-serif;color:var(--text);background:var(--white)}
.abs{position:absolute}
.head{font-family:"Oswald",sans-serif;font-weight:500;text-transform:uppercase}

.topbar{left:0;top:0;width:1200px;height:25px;background:var(--brown);color:#fff;font-size:11px;font-weight:700}
.topbar .call{left:192px;top:5px}
.topbar .call span{color:var(--orange)}
.topbar .follow{left:970px;top:5px;display:flex;gap:3px;align-items:center}
.dot{display:inline-block;width:12px;height:12px;border-radius:50%;background:var(--orange)}

.hero{left:0;top:25px;width:1200px;height:645px;
  background:linear-gradient(180deg,#cfe2f3 0%,#e9f1f8 30%,#dfe7ee 50%,#6f8a58 56%,#7d8e5d 66%,#a13a36 74%,#8a7b5c 84%,#7e8c5a 100%)}
.nav{top:60px;font-size:19px;color:var(--brown)}
.brand{left:450px;top:45px;font-size:30px;color:var(--brown);letter-spacing:2px;display:flex;align-items:center;gap:10px}
.brand .dot{width:28px;height:28px}
.quote-nav{left:1003px;top:49px;width:127px;height:32px;border-radius:16px;background:var(--brown);color:var(--orange);font-size:14px;text-align:center;line-height:32px}
.hero-title{left:0;top:146px;width:1200px;text-align:center;font-size:40px;line-height:42px;color:var(--brown)}
.btn-dark{left:492px;top:264px;width:111px;height:32px;border-radius:16px;background:var(--brown);color:var(--orange);font-size:14px;text-align:center;line-height:32px}
.btn-line{left:630px;top:264px;width:111px;height:32px;border-radius:16px;border:1.5px solid var(--orange);color:var(--brown);font-size:14px;text-align:center;line-height:29px}

.welcome-name{left:117px;top:758px;color:var(--brown)}
.welcome-name .small{font-size:15px;display:block;margin-left:70px}
.welcome-name .big{font-size:36px;letter-spacing:2px;display:flex;align-items:center;gap:12px}
.welcome-name .big .dot{width:56px;height:56px}
.intro{left:117px;top:853px;width:420px;font-size:12.5px;line-height:16px;text-align:justify}
.intro p{margin-bottom:16px}
.photo-horses{left:576px;top:778px;width:457px;height:249px;background:linear-gradient(180deg,#3f6a2c 0%,#6d9a3a 45%,#8dbd46 100%)}
.feature{top:1062px;display:flex;gap:12px}
.feature .dot{width:37px;height:37px;flex:none;border:3px solid #fde0b0}
.feature h4{font-size:14px;font-weight:700;color:var(--brown);line-height:16px}
.feature p{font-size:10px;line-height:12px;color:var(--brown);width:200px}
.orn{background:var(--brown);border-radius:4px}

.services{left:0;top:1224px;width:1200px;height:1109px;background:linear-gradient(180deg,#2e2a26 0%,#3d3326 30%,#4a3c28 70%,#3a2f22 100%)}
.services-title{left:0;top:1290px;width:1200px;text-align:center;font-size:44px;color:var(--orange);letter-spacing:1px}
.photo-bed{left:48px;top:1417px;width:544px;height:377px;background:linear-gradient(160deg,#6b4a22 0%,#d9a441 45%,#c98a2c 100%)}
.photo-feed{left:618px;top:1417px;width:545px;height:377px;background:linear-gradient(110deg,#8a6436 0%,#d8c3a2 55%,#2b2620 100%)}
.card{top:1794px;width:545px;height:484px;background:var(--brown-mid);color:#fff;padding:32px 50px 0 50px}
.card h3{font-size:32px;color:var(--orange);letter-spacing:1px;margin-left:22px}
.card .rule{width:52px;height:2px;background:var(--orange);margin:6px 0 0 22px}
.card p{font-size:15px;line-height:16px;margin-top:40px;text-align:justify}
.card ul{list-style:none;margin-top:30px}
.card li{font-size:14.5px;line-height:24px;display:flex;align-items:center;gap:8px}
.card li svg{flex:none}
.read{display:inline-block;margin-top:28px;width:110px;height:32px;border-radius:16px;background:var(--orange-deep);color:var(--brown);font-size:10px;font-weight:700;letter-spacing:1px;text-align:center;line-height:32px}

.newsletter{left:0;top:2333px;width:1200px;height:205px;background:linear-gradient(180deg,#c9d4de 0%,#e4e8ea 55%,#a89a5e 85%,#7f7a3e 100%)}
.photo-mares{left:10px;top:2370px;width:260px;height:160px;background:linear-gradient(180deg,#a35a25,#7a3f1a);border-radius:40px 60px 10px 10px}
.news-title{left:344px;top:2383px;font-size:32px;color:var(--brown);letter-spacing:1px}
.news-input{left:315px;top:2440px;width:710px;height:50px;background:#fff;border:1px solid #999;font-size:14px;color:#444;padding:15px 40px}
.news-btn{left:1025px;top:2440px;width:126px;height:50px;background:var(--brown);color:#fff;font-size:15px;font-weight:700;text-align:center;line-height:50px}

.footer{left:0;top:2538px;width:1200px;height:231px;background:var(--brown);color:#fff}
.foot-brand{left:120px;top:2650px;font-size:34px;letter-spacing:3px;color:#fff}
.foot-brand-mark{left:223px;top:2588px;width:48px;height:48px}
.foot-h{font-size:15px;color:var(--orange);text-decoration:underline}
.foot-list{font-size:11.5px;line-height:18.5px;list-style:none}
.foot-list li{display:flex;align-items:center;gap:8px}
.tri{width:0;height:0;border-left:6px solid var(--orange);border-top:4px solid transparent;border-bottom:4px solid transparent}
.foot-mail{left:910px;top:2616px;width:162px;height:27px;display:flex}
.foot-mail div:first-child{flex:1;background:#fff;color:#888;font-size:9px;padding:8px 12px}
.foot-mail div:last-child{width:27px;background:var(--orange-deep)}
.bottom{left:0;top:2769px;width:1200px;height:39px;background:var(--orange-deep);color:var(--brown);font-size:13px}
</style>
</head>
<body>

<div class="abs topbar">
  <div class="abs call">Call Us : <span>+1 555 010 2040</span></div>
  <div class="abs follow">Follow Us: <i class="dot"></i><i class="dot"></i><i class="dot"></i><i class="dot"></i><i class="dot"></i></div>
</div>

<header class="abs hero" role="img" aria-label="Aerial photo of red barns, stables and fenced paddocks under a cloudy sky"></header>
<nav>
  <div class="abs head nav" style="left:135px">Home</div>
  <div class="abs head nav" style="left:232px">About</div>
  <div class="abs head nav" style="left:335px">Feed</div>
  <div class="abs head nav" style="left:800px;top:54px;font-size:17px">Bedding</div>
  <div class="abs head nav" style="left:902px;top:54px;font-size:17px">Contact Us</div>
  <div class="abs head brand"><i class="dot"></i>Harvest Hollow</div>
  <div class="abs head quote-nav">Request Qoute</div>
</nav>
<h1 class="abs head hero-title">The Best Bedding &amp; Feed For<br>Your Horse Livestock Or Household Pet</h1>
<div class="abs head btn-dark">Contact Us</div>
<div class="abs head btn-line">Request Quote</div>

<section>
  <div class="abs head welcome-name">
    <span class="small">Welcome to</span>
    <span class="big"><i class="dot"></i>Harvest Hollow</span>
  </div>
  <div class="abs intro">
    <p>Looking for the best bedding and feed for your horse, livestock or household pet look no further. We use premium locally sourced straw and hay in all of our products and are committed in providing quality products and service.</p>
    <p>Your animal deserves the very best in health and comfort to keep them healthy, strong and happy. Our products are designed for horses, livestock (goats, cattle and sheep), small caged animals (rabbits, guinea pigs and more).</p>
    <p>Harvest Hollow offers supply and delivery of fresh bedding as well as removal of waste bedding. Let us deliver you a container of fresh straw and haul your waste bedding away. A full service solution that is sustainable and responsible.</p>
  </div>
  <div class="abs photo-horses" role="img" aria-label="Photo of three horses grazing in a green pasture by a wooden fence"></div>

  <div class="abs feature" style="left:117px"><i class="dot"></i><div><h4>QUALITY GUARANTEED</h4><p>Grown for quality - 100% natural with no chemicals or additives</p></div></div>
  <div class="abs orn" style="left:380px;top:1052px;width:8px;height:55px" role="img" aria-label="Wheat stalk ornament"></div>
  <div class="abs feature" style="left:435px"><i class="dot"></i><div><h4>FULL SERVICE SOLUTION</h4><p>Dedicated in providing a full service solution of bedding supply &amp; waste removal</p></div></div>
  <div class="abs orn" style="left:712px;top:1052px;width:8px;height:55px" role="img" aria-label="Wheat stalk ornament"></div>
  <div class="abs feature" style="left:768px"><i class="dot"></i><div><h4>CONVENIENT &amp; COST EFFECTIVE</h4><p style="width:220px">Compressed bags, pellets or bulk products saving in shipping costs</p></div></div>
</section>

<section class="abs services" role="img" aria-label="Dimmed photo of round hay bales in a field"></section>
<h2 class="abs head services-title">Our Services</h2>
<div class="abs photo-bed" role="img" aria-label="Photo of a mare and foal resting on straw bedding"></div>
<div class="abs photo-feed" role="img" aria-label="Close photo of a horse eating hay"></div>

<article class="abs card" style="left:48px">
  <h3 class="head">Bedding</h3><div class="rule"></div>
  <p>Hay cubes and pellets are made from premium hay offering a variety of animals a feed that is non-GMO and packed with natural nutrients. These pellets and cubes are less bulky to handle, store and ship.As well, they reduce the amount of wasted feed.</p>
  <ul>
    <li><svg width="12" height="12" viewBox="0 0 12 12"><circle cx="6" cy="6" r="6" fill="#f7a11a"/><path d="M3.2 6.2l2 2 3.6-4" stroke="#4a2c18" stroke-width="1.6" fill="none"/></svg>100% Natural Chopped Straw</li>
    <li><svg width="12" height="12" viewBox="0 0 12 12"><circle cx="6" cy="6" r="6" fill="#f7a11a"/><path d="M3.2 6.2l2 2 3.6-4" stroke="#4a2c18" stroke-width="1.6" fill="none"/></svg>Low Dust</li>
    <li><svg width="12" height="12" viewBox="0 0 12 12"><circle cx="6" cy="6" r="6" fill="#f7a11a"/><path d="M3.2 6.2l2 2 3.6-4" stroke="#4a2c18" stroke-width="1.6" fill="none"/></svg>Chemical &amp; Additive Free</li>
    <li><svg width="12" height="12" viewBox="0 0 12 12"><circle cx="6" cy="6" r="6" fill="#f7a11a"/><path d="M3.2 6.2l2 2 3.6-4" stroke="#4a2c18" stroke-width="1.6" fill="none"/></svg>Clean &amp; Highly Absorbent</li>
    <li><svg width="12" height="12" viewBox="0 0 12 12"><circle cx="6" cy="6" r="6" fill="#f7a11a"/><path d="M3.2 6.2l2 2 3.6-4" stroke="#4a2c18" stroke-width="1.6" fill="none"/></svg>Cheaper than Wood Shavings</li>
    <li><svg width="12" height="12" viewBox="0 0 12 12"><circle cx="6" cy="6" r="6" fill="#f7a11a"/><path d="M3.2 6.2l2 2 3.6-4" stroke="#4a2c18" stroke-width="1.6" fill="none"/></svg>Economic – less used &amp; less wasted</li>
    <li><svg width="12" height="12" viewBox="0 0 12 12"><circle cx="6" cy="6" r="6" fill="#f7a11a"/><path d="M3.2 6.2l2 2 3.6-4" stroke="#4a2c18" stroke-width="1.6" fill="none"/></svg>Environmentally Friendly – Recyclable &amp; Compostable</li>
  </ul>
  <span class="read">READ MORE</span>
</article>

<article class="abs card" style="left:623px">
  <h3 class="head">Feeding</h3><div class="rule"></div>
  <p>Hay cubes and pellets are made from premium hay offering a variety of animals a feed that is non-GMO and packed with natural nutrients. These pellets and cubes are less bulky to handle, store and ship.As well, they reduce the amount of wasted feed.</p>
  <ul>
    <li><svg width="12" height="12" viewBox="0 0 12 12"><circle cx="6" cy="6" r="6" fill="#f7a11a"/><path d="M3.2 6.2l2 2 3.6-4" stroke="#4a2c18" stroke-width="1.6" fill="none"/></svg>100% Natural</li>
    <li><svg width="12" height="12" viewBox="0 0 12 12"><circle cx="6" cy="6" r="6" fill="#f7a11a"/><path d="M3.2 6.2l2 2 3.6-4" stroke="#4a2c18" stroke-width="1.6" fill="none"/></svg>Chemical &amp; Additive Free</li>
    <li><svg width="12" height="12" viewBox="0 0 12 12"><circle cx="6" cy="6" r="6" fill="#f7a11a"/><path d="M3.2 6.2l2 2 3.6-4" stroke="#4a2c18" stroke-width="1.6" fill="none"/></svg>Available in Pellets or Cubes</li>
    <li><svg width="12" height="12" viewBox="0 0 12 12"><circle cx="6" cy="6" r="6" fill="#f7a11a"/><path d="M3.2 6.2l2 2 3.6-4" stroke="#4a2c18" stroke-width="1.6" fill="none"/></svg>High Protein Content</li>
    <li><svg width="12" height="12" viewBox="0 0 12 12"><circle cx="6" cy="6" r="6" fill="#f7a11a"/><path d="M3.2 6.2l2 2 3.6-4" stroke="#4a2c18" stroke-width="1.6" fill="none"/></svg>Eliminate Waste In Feeding</li>
    <li><svg width="12" height="12" viewBox="0 0 12 12"><circle cx="6" cy="6" r="6" fill="#f7a11a"/><path d="M3.2 6.2l2 2 3.6-4" stroke="#4a2c18" stroke-width="1.6" fill="none"/></svg>Clean - Eliminates Dust From Feeding Baled Hay</li>
    <li><svg width="12" height="12" viewBox="0 0 12 12"><circle cx="6" cy="6" r="6" fill="#f7a11a"/><path d="M3.2 6.2l2 2 3.6-4" stroke="#4a2c18" stroke-width="1.6" fill="none"/></svg>Cost Effective</li>
  </ul>
  <span class="read" style="margin-top:48px">READ MORE</span>
</article>

<section class="abs newsletter" role="img" aria-label="Cloudy sky over a grassy meadow"></section>
<div class="abs photo-mares" role="img" aria-label="Photo of a chestnut mare and foal grazing"></div>
<h2 class="abs head news-title">Subscribe to Newsletter</h2>
<div class="abs news-input">Enter Your Email</div>
<div class="abs news-btn">SUBSCRIBE</div>

<footer class="abs footer"></footer>
<i class="abs dot foot-brand-mark"></i>
<div class="abs head foot-brand">Harvest Hollow</div>

<div class="abs foot-h" style="left:451px;top:2584px">QUICK LINKS</div>
<ul class="abs foot-list" style="left:452px;top:2614px;color:#fff">
  <li><i class="tri"></i>Home</li><li><i class="tri"></i>About</li><li><i class="tri"></i>Feed</li><li><i class="tri"></i>Bedding</li><li><i class="tri"></i>Contact Us</li>
</ul>

<div class="abs foot-h" style="left:654px;top:2586px">CONTACT US</div>
<ul class="abs foot-list" style="left:654px;top:2617px;color:#fff">
  <li><svg width="10" height="12" viewBox="0 0 10 12"><path d="M5 0a4 4 0 0 1 4 4c0 3-4 8-4 8S1 7 1 4a4 4 0 0 1 4-4z" fill="#f7a11a"/><circle cx="5" cy="4" r="1.5" fill="#3c2415"/></svg>412 Meadow Row</li>
  <li style="padding-left:18px">Fairbanks, Alaska 99701</li>
  <li><svg width="10" height="10" viewBox="0 0 10 10"><path d="M2 0l2 2.5-1.2 1.3a6 6 0 0 0 3.4 3.4L7.5 6 10 8 8.5 10C4 10 0 6 0 1.5z" fill="#f7a11a"/></svg>555-010-7788</li>
  <li><svg width="10" height="8" viewBox="0 0 10 8"><rect width="10" height="8" fill="#f7a11a"/><path d="M0 0l5 4 5-4" stroke="#3c2415" fill="none"/></svg>hello@harvesthollow.example</li>
  <li><svg width="10" height="10" viewBox="0 0 10 10"><circle cx="5" cy="5" r="4.3" stroke="#f7a11a" fill="none"/><path d="M1 5h8M5 1v8" stroke="#f7a11a" stroke-width=".8"/></svg>harvesthollow.example</li>
</ul>

<div class="abs foot-h" style="left:913px;top:2584px">NEWSLETTER</div>
<div class="abs foot-mail"><div>Email Address</div><div></div></div>
<div class="abs foot-h" style="left:913px;top:2656px">FOLLOW US</div>
<div class="abs" style="left:913px;top:2687px;display:flex;gap:3px"><i class="dot" style="width:17px;height:17px;background:#fff"></i><i class="dot" style="width:17px;height:17px;background:#fff"></i><i class="dot" style="width:17px;height:17px;background:#fff"></i><i class="dot" style="width:17px;height:17px;background:#fff"></i><i class="dot" style="width:17px;height:17px;background:#fff"></i></div>

<div class="abs bottom">
  <span class="abs" style="left:127px;top:11px">Copyright © 2021, Northfield Studio, All Right Reserved</span>
  <span class="abs" style="left:929px;top:11px">Delivery in Canada &amp; USA</span>
</div>

</body>
</html>
```